Commercial Rooftop Solar business needs a website

We need a website with fantastic appeal for a new company based in Melbourne called Tallow Ridge Energy. We design and install solar energy systems for commercial applications across Australia. Our market is to focus on small to medium businesses looking for solar solutions, but we will also provide our service for residential customers. We would like a beautiful 'front page' feel to our home page, using photographs of solar PV systems and/or natural imagery. Our logo uses the colours orange and black, which could easily be echoed in photographic imagery of sunset and sunrise, for example. The design should communicate quiet confidence and professionalism to a corporate marketplace.

NEW POINTS FOR BRIEF: This design also needs to be flexible to allow for additional future content, including a Support page with sub pages, FAQ's, and a Blog.

As part of this design project, we will require the coding for the website to be completed by the designer.

We have seen some websites, which we like the look and feel of: these are listed below.

brightvanepower.com.au:

• Beautiful images underlaying brief text selling points.
• Simple ‘front cover’ style home page with elegant drop-down menu, stylish simple font style.
• Home page invites exploration through the menu links, rather than trying to provide all the information up front.
• Company logo and name in the top left hand corner, contact details accessible at top right hand, seems consistent in most sites.

kelpworks.com.au

rumbofield.com:
• Same element as the others is the front-page style home page with beautiful images underlying text.

We have a webpage that we started uploading content to. You can use some of the content there in your designs: www.tallowridgeenergy.com.au

Technical Specifications:
PAGES:

Home

About Us

Solutions - Commercial
- Residential

Products - Solar Panels - Vorla Heron, Vorla TELD, Vorla QB
- Solar Inverters - Kestamo, BrilQuill
- Monitoring systems - Dunmere Metrics
- Batteries - RW

- Datasheets have been provided for reference but if it's too much work, you can use generic text and we will provide content later.

Contact Us

FUTURE PAGES (Please consider in structure, where links could be placed):

Support

FAQ's

Blog.

We could provide some content for the Support page soon, but the Blog and FAQ's are future pages which we don't want highlighted in the design as we don't yet have content.

Phone: 1800 7 BIRCH
Email: sales@tallowridgeenergy.com.au

Currently, I do not have images and text available. Please
use placeholders in the meantime. The final text and images will be uploaded for the winner once a winning design has been selected.

Target Market(s)

Primary focus is on small to medium sized business owners. Those owners will have a house which may be suitable for solar so we want to cater to residential deeper in the website.

Industry/Entity Type

Solar Energy

Coding

Coded - Design and coding required

Number of Pages Required

5+ page

Colors
f78f20
0255a3

Requirements
Must have
• Logo as per attachments.
Nice to have
• Logo can have alternate colours Eg. White on Orange or Black etc. provided colour correct logo is shown somewhere eg. footer or contact page.
• In the active site, I'd like to have:
• Very slowly zooming images - barely perceptible.
• Title text that rolls into place
• Subtle movements
• See https://plumtally.com.au/ for example

```html
<!DOCTYPE html>
<html lang="en">
<head>
<meta charset="utf-8">
<title>Tallow Ridge Energy</title>
<link rel="stylesheet" href="https://fonts.googleapis.com/css2?family=Mulish:wght@300;400;600;700&family=Open+Sans:wght@400;600&display=swap">
<style>
:root{
  --orange:#f15a22;
  --orange-soft:#f2784a;
  --ink:#1f1f1f;
  --text:#333333;
  --muted:#9a9a9a;
  --panel:#ebebeb;
  --footer:#2b2626;
  --footer-deep:#1c1919;
  --white:#ffffff;
  --teal:#1aa39a;
}
*{box-sizing:border-box;margin:0;padding:0}
html,body{width:1200px;height:2740px;overflow:hidden}
body{position:relative;background:var(--white);font-family:"Open Sans",sans-serif;color:var(--text)}
.block{position:absolute;left:0;width:1200px}

/* header */
.site-header{top:0;height:110px;background:var(--white);border-top:3px solid var(--teal)}
.brand{position:absolute;left:118px;top:38px;display:flex;align-items:center;gap:10px;font-family:"Mulish",sans-serif;font-weight:700;font-size:22px;color:var(--orange);letter-spacing:.5px}
.brand-dot{width:30px;height:30px;border-radius:50%;background:var(--ink)}
.main-nav{position:absolute;left:424px;top:46px;display:flex;gap:0}
.main-nav a{position:relative;font-family:"Mulish",sans-serif;font-size:17px;color:var(--ink);text-decoration:none;margin-right:40px}
.main-nav a.active::before{content:"";position:absolute;left:-4px;right:-4px;top:-49px;height:8px;background:var(--orange)}
.header-phone{position:absolute;left:912px;top:44px;display:flex;align-items:center;gap:6px;font-family:"Mulish",sans-serif;font-size:20px;color:var(--ink)}

/* hero */
.hero{top:110px;height:557px;background:linear-gradient(180deg,#8a6f78 0%,#d78a55 22%,#e9a062 36%,#7d6a80 48%,#4d5ca6 60%,#3a4ba0 78%,#5060b0 100%)}
.hero-title{position:absolute;left:0;width:1200px;top:178px;text-align:center;font-family:"Mulish",sans-serif;font-weight:400;font-size:38px;line-height:48px;color:var(--white);letter-spacing:.5px}
.btn{display:inline-block;font-family:"Mulish",sans-serif;font-size:15px;text-transform:uppercase;text-align:center;text-decoration:none}
.btn-solid{position:absolute;left:524px;top:293px;width:160px;height:42px;line-height:42px;background:var(--orange);color:var(--white);font-size:17px}
.slider-dots{position:absolute;left:555px;top:522px;display:flex;gap:9px}
.slider-dots span{width:14px;height:14px;border-radius:50%;border:2px solid var(--white)}
.slider-dots span.on{background:var(--white)}

/* about */
.about{top:667px;height:425px;text-align:center}
.about-mark{position:absolute;left:578px;top:44px;width:44px;height:44px;border-radius:50%;background:var(--ink)}
.section-title{font-family:"Mulish",sans-serif;font-weight:600;font-size:29px;color:var(--ink);letter-spacing:.5px}
.about .section-title{position:absolute;left:0;width:1200px;top:100px}
.about-copy{position:absolute;left:200px;width:800px;top:158px;font-size:13.5px;line-height:24px;color:var(--muted)}
.about-copy p+p{margin-top:10px}
.btn-outline{position:absolute;left:521px;top:324px;width:160px;height:42px;line-height:38px;border:2px solid var(--orange);color:var(--orange);font-size:16px}

/* solutions */
.solutions{top:1092px;height:512px;background:var(--panel)}
.solutions .section-title{position:absolute;left:0;width:1200px;top:42px;text-align:center;font-weight:400}
.solution-card{position:absolute;top:95px;height:358px;width:481px;text-align:center;color:var(--white)}
.solution-card.commercial{left:117px;background:var(--orange)}
.solution-card.residential{left:598px;background:#000}
.notch{position:absolute;left:571px;top:95px;width:0;height:0;border-left:27px solid transparent;border-right:27px solid transparent;border-top:27px solid var(--panel)}
.solution-icon{display:block;margin:48px auto 0;width:96px;height:96px;border-radius:50%;border:9px solid var(--white)}
.solution-name{margin-top:24px;font-family:"Mulish",sans-serif;font-weight:600;font-size:22px;letter-spacing:.5px}
.solution-text{margin:8px auto 0;width:340px;font-size:13px;line-height:25px;opacity:.55}
.btn-ghost{margin-top:22px;width:126px;height:36px;line-height:32px;border:2px solid var(--white);color:var(--white);font-size:12px}

/* why */
.why{top:1604px;height:465px;background:linear-gradient(180deg,#54405e 0%,#7b5a6e 20%,#c47f5a 42%,#e9b25a 52%,#6a5a70 66%,#2f3c68 82%,#233055 100%)}
.why-content{position:absolute;left:122px;top:96px;width:440px;color:var(--white)}
.why-title{font-family:"Mulish",sans-serif;font-weight:600;font-size:29px;letter-spacing:.5px}
.why-content p{font-size:14px;line-height:20px;margin-top:12px}
.why-content p+p{margin-top:14px}
.why .btn-outline-light{position:absolute;left:122px;top:303px;width:146px;height:42px;line-height:38px;border:2px solid var(--white);color:var(--white);font-size:14px}

/* newsletter */
.newsletter{top:2069px;height:307px;background:linear-gradient(180deg,#e7622d 0%,#ef7446 55%,#f08458 100%);text-align:center;color:var(--white)}
.newsletter-title{position:absolute;left:0;width:1200px;top:72px;font-family:"Mulish",sans-serif;font-weight:700;font-size:35px;letter-spacing:.5px}
.newsletter-copy{position:absolute;left:270px;width:660px;top:128px;font-size:13px;line-height:22px}
.newsletter-form{position:absolute;left:274px;top:191px;display:flex;gap:13px}
.newsletter-form .field{width:482px;height:42px;background:var(--white);color:#555;text-align:left;padding-left:16px;line-height:42px;font-size:14px}
.newsletter-form .submit{width:159px;height:42px;line-height:42px;background:var(--footer);color:var(--white);font-family:"Mulish",sans-serif;font-size:15px}

/* footer */
.site-footer{top:2376px;height:294px;background:var(--footer);color:var(--white)}
.footer-col{position:absolute;top:60px}
.footer-col h3{font-family:"Mulish",sans-serif;font-weight:400;font-size:22px;margin-bottom:14px}
.footer-col li{list-style:none;font-size:13.5px;line-height:29px;display:flex;align-items:center;gap:12px}
.col-company{left:133px}.col-resources{left:353px}.col-contact{left:550px}.col-social{left:890px}
.social-row{display:flex;gap:8px;margin-top:2px}
.social-row span{width:37px;height:37px;border-radius:50%;border:2px solid var(--white)}
.copyright{top:2670px;height:70px;background:var(--footer-deep);color:#bbbbbb;font-size:12px;text-align:center;line-height:70px}
</style>
</head>
<body>

<header class="block site-header">
  <div class="brand"><span class="brand-dot"></span>Tallow Ridge Energy</div>
  <nav class="main-nav">
    <a class="active" href="#">HOME</a>
    <a href="#">ABOUT US</a>
    <a href="#">SOLUTIONS</a>
    <a href="#">CONTACT US</a>
  </nav>
  <div class="header-phone">
    <svg width="24" height="24" viewBox="0 0 24 24" fill="none" stroke="#f15a22" stroke-width="2"><path d="M5 3h4l2 5-3 2a12 12 0 0 0 6 6l2-3 5 2v4a2 2 0 0 1-2 2A17 17 0 0 1 3 5a2 2 0 0 1 2-2z"/></svg>
    (555) 014 2230
  </div>
</header>

<section class="block hero" role="img" aria-label="Photo of rooftop solar panels under a sunset sky with mountains">
  <h1 class="hero-title">DESIGN AND INSTALL SOLAR ENERGY<br>SYSTEMS FOR COMMERCIAL</h1>
  <a class="btn btn-solid" href="#">Read more</a>
  <div class="slider-dots"><span class="on"></span><span></span><span></span><span></span></div>
</section>

<section class="block about">
  <span class="about-mark"></span>
  <h2 class="section-title">ABOUT TALLOW RIDGE ENERGY</h2>
  <div class="about-copy">
    <p>commodo a mi Morbi ornare gravida elit Integer congue augue et malesuada iaculis ipsum dui aliquet felis at cursus magna nisl nec elit Praesent elementum elit at tellus nec ultricies sit</p>
    <p>Amet porttitor mattis enim In massa libero interdum nec interdum vel blandit sed nulla In ullamcorper est eget tempor cursus neque mi consectetuer mi a ultricies massa est sed nisl Class aptent taciti sociosqu ad litora torquent per conubia nostra per inceptos hymenaeos Proin nulla arcu nonumm</p>
  </div>
  <a class="btn btn-outline" href="#">Read more</a>
</section>

<section class="block solutions">
  <h2 class="section-title">OUR SOLUTION</h2>
  <article class="solution-card commercial">
    <span class="solution-icon"></span>
    <h3 class="solution-name">COMMERCIAL</h3>
    <p class="solution-text">Class aptent taciti sociosqu ad litora torquent per conubia nostra per inceptos hymenaeos Proin nulla</p>
    <a class="btn btn-ghost" href="#">Read more</a>
  </article>
  <article class="solution-card residential">
    <span class="solution-icon"></span>
    <h3 class="solution-name">RESIDENTIAL</h3>
    <p class="solution-text">Class aptent taciti sociosqu ad litora torquent per conubia nostra per inceptos hymenaeos Proin nulla</p>
    <a class="btn btn-ghost" href="#">Read more</a>
  </article>
  <span class="notch"></span>
</section>

<section class="block why" role="img" aria-label="Photo of a solar panel field at sunrise under a purple sky">
  <div class="why-content">
    <h2 class="why-title">WHY WE ARE</h2>
    <p>Praesent elementum elit at tellus nec ultricies sit amet porttitor mattis enim In massa libero interdum nec interdum</p>
    <p>eget tempor cursus neque mi consectetuer mi a ultricies massa est sed nisl Class aptent taciti sociosqu ad litora torquent per conubia nostra per inceptos hymenaeos Proin nulla arcu nonummy luctus dictum eget fermentum et lorem</p>
  </div>
  <a class="btn btn-outline-light" href="#">Read more</a>
</section>

<section class="block newsletter" role="img" aria-label="Orange tinted photo of solar panels in front of city buildings">
  <h2 class="newsletter-title">JOIN THE NEWSLETTER</h2>
  <p class="newsletter-copy">Sed ut perspiciatis unde omnis iste natus error sit voluptatem accusantium doloremque laudantium, totam rem aperiam, eaque ipsa quae ab illo inventore veritatis et quasi</p>
  <div class="newsletter-form">
    <div class="field">email</div>
    <div class="submit">JOIN NOW!</div>
  </div>
</section>

<footer class="block site-footer">
  <div class="footer-col col-company">
    <h3>Company</h3>
    <ul><li>About Us</li><li>Contact Us</li><li>Privacy Policy</li><li>Terms &amp; Condition</li></ul>
  </div>
  <div class="footer-col col-resources">
    <h3>Resources</h3>
    <ul><li>Solutions</li><li>Services</li><li>Projects</li></ul>
  </div>
  <div class="footer-col col-contact">
    <h3>Contact Us</h3>
    <ul>
      <li><svg width="14" height="16" viewBox="0 0 14 16"><path d="M7 0a6 6 0 0 0-6 6c0 4 6 10 6 10s6-6 6-10a6 6 0 0 0-6-6zm0 8.5A2.5 2.5 0 1 1 7 3.5a2.5 2.5 0 0 1 0 5z" fill="#fff"/></svg>48 Larkspur Lane, Melbourne VIC 3000</li>
      <li><svg width="15" height="15" viewBox="0 0 24 24" fill="none" stroke="#fff" stroke-width="2"><path d="M5 3h4l2 5-3 2a12 12 0 0 0 6 6l2-3 5 2v4a2 2 0 0 1-2 2A17 17 0 0 1 3 5a2 2 0 0 1 2-2z"/></svg>555.014.7781</li>
      <li><svg width="15" height="12" viewBox="0 0 15 12" fill="none" stroke="#fff" stroke-width="1.4"><rect x="1" y="1" width="13" height="10"/><path d="M1 1l6.5 5.5L14 1"/></svg>info@tallowridgeenergy.com.au</li>
    </ul>
  </div>
  <div class="footer-col col-social">
    <h3>Stay in Touch</h3>
    <div class="social-row" aria-label="Social links"><span></span><span></span><span></span><span></span></div>
  </div>
</footer>

<div class="block copyright">© 2016 Tallow Ridge Energy &nbsp;All right reserved</div>

</body>
</html>
```